Crestline Leadership Roadmap

I've included a mock up of what I like. This design needs to be made better. I like the top section layout. It needs 5 circles for:

Please create a webpage based on this design, but improve it. Use the letterhead and business card brand you created for me to make the brand look seamless.

I love the circles - please make 5 of them the same size (can be 1 lines)

Here is the text for the circles:

Headline: Your Guided Path to Transformation
Text
Step 1: The Initial Consultation
text
Step 2: Deep-Dive Discovery and Assessment
text
Step 3: Synthesis and Strategy Formulation
text
Step 4: The Strategic Debrief Session
Text
Step 5: Implementation and Ongoing Support
Text

Also, there are many sections to this page including:

Introduction
Copy
Copy
Bio
CTA
FAQ's

Please make it interesting.

Use the colors of the mockup and my website: Corwin Adeley.com
I am including my letterhead and business card for brand coherence.

Use the fonts on my website. CorwinAdeley.com

I will need all files to send to the developer. We must have ALL the art files.

see my website; CorwinAdeley.com

See my uploads

Must have
• all the design files

```html
<!DOCTYPE html>
<html lang="en">
<head>
<meta charset="utf-8">
<title>Crestline Leadership</title>
<link rel="stylesheet" href="https://fonts.googleapis.com/css2?family=Josefin+Sans:wght@400;600;700&family=Open+Sans:wght@400;600;700&display=swap">
<style>
:root{
  --navy:#1c2449;
  --navy-deep:#131a38;
  --gold:#c79a45;
  --gold-soft:#e2c593;
  --ink:#1c2449;
  --text:#5b5f6e;
  --white:#ffffff;
  --panel:#efeff1;
  --head:"Josefin Sans",sans-serif;
  --body:"Open Sans",sans-serif;
}
*{box-sizing:border-box;margin:0;padding:0}
html,body{width:1200px;height:5102px;overflow:hidden;background:var(--white);font-family:var(--body);color:var(--text)}
.page{position:relative;width:1200px;height:5102px}
.abs{position:absolute}
.btn{position:absolute;display:flex;align-items:center;justify-content:center;background:var(--gold);color:var(--white);font-family:var(--body);font-weight:600;font-size:13px;letter-spacing:.5px;border-radius:30px;text-transform:uppercase}
.rule{position:absolute;height:4px;background:var(--gold);width:120px}
.title{position:absolute;left:0;width:1200px;text-align:center;font-family:var(--head);font-weight:400;color:var(--ink);font-size:40px;line-height:1.3}
.title b{font-weight:600}

/* top bar + nav */
.topbar{top:0;left:0;width:1200px;height:40px;background:var(--navy)}
.topbar .tag{left:110px;top:11px;color:var(--white);font-size:13px}
.social{width:28px;height:28px;border-radius:50%;border:2px solid var(--white);background:#2a6db3}
.nav{top:40px;left:0;width:1200px;height:63px;background:var(--white)}
.nav a{position:absolute;top:24px;font-size:13.5px;color:var(--ink);text-decoration:none}
.nav a.on{color:var(--gold);font-weight:700}
.brand-badge{top:12px;left:487px;width:226px;height:165px;background:var(--white);clip-path:polygon(0 0,100% 0,88% 100%,12% 100%);z-index:3}
.brand-badge .mark{position:absolute;left:78px;top:14px;width:70px;height:70px;border-radius:50%;border:3px solid var(--gold)}
.brand-badge .name{position:absolute;left:0;top:132px;width:226px;text-align:center;font-family:var(--head);font-weight:600;font-size:14px;color:var(--navy);letter-spacing:.5px}

/* hero */
.hero{top:103px;left:0;width:1200px;height:640px}
.hero .photo{position:absolute;inset:0;background:linear-gradient(180deg,#3a4a70 0%,#243258 45%,#1a2448 100%)}
.hero h1{position:absolute;top:128px;left:0;width:1200px;text-align:center;color:var(--white);font-family:var(--head);font-weight:600;font-size:62px;line-height:78px;letter-spacing:1px}
.hero p{position:absolute;top:307px;left:0;width:1200px;text-align:center;color:var(--white);font-family:var(--head);font-size:24px;line-height:36px}
.hero svg{position:absolute;left:0;top:0}

/* steps */
.step{position:absolute;top:1004px;width:200px;text-align:center}
.ring{position:relative;margin:0 auto;width:134px;height:134px;border-radius:50%;background:var(--gold-soft)}
.ring .arc{position:absolute;left:10px;top:10px;width:114px;height:114px;border-radius:50%;background:conic-gradient(from 200deg,var(--navy) 0 170deg,transparent 170deg)}
.ring .core{position:absolute;left:22px;top:22px;width:90px;height:90px;border-radius:50%;background:var(--gold);display:flex;align-items:center;justify-content:center}
.ring .num{position:absolute;left:54px;top:-6px;width:26px;height:26px;border-radius:50%;background:var(--gold);border:2px solid var(--white);color:var(--white);font-size:13px;font-weight:700;display:flex;align-items:center;justify-content:center}
.step h3{margin-top:26px;font-family:var(--head);font-weight:400;font-size:16px;line-height:21px;color:var(--ink)}
.step p{margin-top:8px;font-size:12.5px;line-height:19px;color:var(--text)}

/* about band */
.about{top:1382px;left:0;width:1200px;height:523px;background:var(--navy)}
.about h2{position:absolute;left:647px;top:72px;font-family:var(--head);font-weight:400;font-size:42px;color:var(--white)}
.about h2 b{color:var(--gold);font-weight:600}
.about .lead{position:absolute;left:645px;top:150px;color:var(--gold);font-size:13px;font-weight:600}
.about .copy{position:absolute;left:647px;top:182px;width:440px;color:var(--white);font-size:13px;line-height:29px;text-align:justify}

/* sectors */
.sector{position:absolute;top:2178px;width:313px;height:349px}
.sector .img{position:absolute;inset:0}
.sector .lbl{position:absolute;top:368px;left:0;font-family:var(--head);font-weight:600;font-size:20px;color:var(--ink)}
.arrow{position:absolute;top:2341px;width:26px;height:26px;border-radius:50%}

/* stats */
.stats{top:2667px;left:111px;width:976px;height:327px;border-radius:6px;background:linear-gradient(90deg,#3a2d35 0%,#8a5a2c 45%,#6b4428 65%,#2d2740 100%)}
.stat{position:absolute;top:87px;width:240px;text-align:center;color:var(--white)}
.stat .ico{margin:0 auto;width:82px;height:82px;border-radius:50%;background:var(--gold-soft);display:flex;align-items:center;justify-content:center}
.stat .ico span{width:62px;height:62px;border-radius:50%;background:var(--gold);display:flex;align-items:center;justify-content:center}
.stat strong{display:block;margin-top:10px;font-family:var(--head);font-weight:400;font-size:26px}
.stat em{display:block;font-style:normal;font-size:15px;line-height:26px}

/* bio */
.bio h2{left:111px;top:3074px;font-family:var(--head);font-weight:400;font-size:44px;color:var(--ink)}
.bio h2 b{font-weight:600}
.bio p{left:111px;width:453px;font-size:12.5px;line-height:27px;color:var(--text);text-align:justify}
.portrait{left:665px;top:3081px;width:412px;height:412px;border-radius:50%;background:radial-gradient(circle at 50% 40%,#c9a58a 0%,#7a5444 45%,#dcdde0 80%)}

/* cta */
.cta{top:3570px;left:111px;width:976px;height:378px;background:linear-gradient(180deg,#1d2132 0%,#141a2e 60%,#202a4a 100%)}
.cta h2{position:absolute;top:62px;width:976px;text-align:center;font-family:var(--head);font-weight:400;font-size:42px;color:var(--white)}
.cta h2 b{font-weight:600}
.cta p{position:absolute;top:148px;left:188px;width:600px;text-align:center;color:var(--white);font-size:13px;line-height:27px}

/* faq */
.faq-item{position:absolute;left:115px;width:489px;height:54px;background:var(--panel);border-radius:4px;display:flex;align-items:center;justify-content:space-between;padding:0 26px;font-size:12.5px;color:var(--ink)}
.faq-item.open{background:var(--gold);color:var(--white);font-weight:600}
.faq-item.open::after{content:"";position:absolute;right:-16px;top:19px;border-left:16px solid var(--gold);border-top:8px solid transparent;border-bottom:8px solid transparent}
.faq-answer{left:650px;top:4162px;width:445px;height:301px;background:var(--panel);border-radius:4px;padding:34px 38px}
.faq-answer h4{font-size:17px;line-height:27px;color:var(--ink);font-weight:600}
.faq-answer p{margin-top:18px;font-size:12.5px;line-height:27px;color:var(--text)}

/* footer */
.footer{top:4640px;left:0;width:1200px;height:462px}
.footer svg{position:absolute;left:0;top:0}
.f-logo{left:143px;top:148px;width:110px;height:110px;border-radius:50%;border:3px solid var(--gold)}
.f-name{left:90px;top:280px;width:220px;text-align:center;font-family:var(--head);font-weight:600;color:var(--white);font-size:16px;letter-spacing:.5px}
.f-note{left:115px;top:322px;width:210px;color:var(--white);font-size:10.5px;line-height:20px}
.f-col h5{font-family:var(--head);font-weight:400;font-size:22px;color:var(--gold)}
.f-col a{display:block;margin-top:18px;color:var(--white);font-size:15px;text-decoration:none}
.f-line{left:111px;top:419px;width:976px;height:1px;background:rgba(255,255,255,.5)}
.f-copy{left:0;top:437px;width:1200px;text-align:center;color:var(--white);font-size:11px}
</style>
</head>
<body>
<div class="page">

  <!-- top bar -->
  <div class="abs topbar">
    <span class="abs tag">Crestline Leadership and Organization Development</span>
    <span class="abs social" style="left:1053px;top:6px" aria-label="Social profile"></span>
  </div>

  <!-- navigation -->
  <nav class="abs nav">
    <a class="on" style="left:111px">Home</a>
    <a style="left:203px">About</a>
    <a style="left:296px">Coaching</a>
    <a style="left:406px">Retreats</a>
    <a style="left:763px">Insights</a>
    <a style="left:864px">Faq's</a>
    <span class="btn" style="left:955px;top:12px;width:133px;height:42px">Contact</span>
  </nav>
  <div class="abs brand-badge">
    <span class="mark"></span>
    <span class="name">CRESTLINE LEADERSHIP</span>
  </div>

  <!-- hero -->
  <section class="abs hero">
    <div class="photo" role="img" aria-label="Mountain landscape with pine trees at dusk"></div>
    <svg width="1200" height="640" viewBox="0 0 1200 640">
      <path d="M0 490 Q600 640 1200 480 L1200 640 L0 640Z" fill="var(--gold)"/>
      <path d="M0 520 Q600 720 1200 500 L1200 640 L0 640Z" fill="var(--white)"/>
      <path d="M0 490 Q600 640 1200 480" fill="none" stroke="var(--navy)" stroke-width="8"/>
    </svg>
    <h1>Support Your Leadership<br>Efforts with Crestline Coaching</h1>
    <p>Introducing Crestline Leadership Coaching<br>and Organization Development</p>
    <span class="btn" style="left:481px;top:408px;width:236px;height:53px">Book a Discovery Call</span>
  </section>

  <!-- guided path -->
  <h2 class="title" style="top:825px">Your Guided<br><b>Path to Transformation</b></h2>
  <span class="rule" style="left:540px;top:942px"></span>

  <div class="step" style="left:104px">
    <div class="ring"><span class="arc"></span><span class="core">
      <svg width="44" height="40" viewBox="0 0 44 40" fill="#fff"><circle cx="14" cy="10" r="7"/><circle cx="31" cy="12" r="6"/><path d="M2 38c0-9 5-15 12-15s12 6 12 15z"/><path d="M24 38c0-8 3-13 8-13s10 5 10 13z"/></svg>
    </span><span class="num">1</span></div>
    <h3>The Initial<br>Consultation</h3>
    <p>Lorem ipsum dolor sit<br>amet, consectetur<br>adipiscing elit,</p>
  </div>
  <div class="step" style="left:304px">
    <div class="ring"><span class="arc"></span><span class="core">
      <svg width="40" height="44" viewBox="0 0 40 44" fill="none" stroke="#fff" stroke-width="3"><rect x="5" y="6" width="28" height="34" rx="3"/><path d="M12 6V2h14v4M11 18h14M11 26h10M11 33h8"/><path d="M36 18L24 32l-4 2 1-4 12-14z" fill="#fff"/></svg>
    </span><span class="num">2</span></div>
    <h3>Deep-Dive Discovery<br>and Assessment</h3>
    <p>Lorem ipsum dolor sit<br>amet, consectetur<br>adipiscing elit,</p>
  </div>
  <div class="step" style="left:502px">
    <div class="ring"><span class="arc"></span><span class="core">
      <svg width="40" height="44" viewBox="0 0 40 44" fill="#fff"><circle cx="20" cy="17" r="10"/><rect x="15" y="28" width="10" height="8" rx="2"/><path d="M20 1v4M4 17h4M32 17h4M8 6l3 3M32 6l-3 3" stroke="#fff" stroke-width="3"/></svg>
    </span><span class="num">3</span></div>
    <h3>Synthesis and<br>Strategy Formulation</h3>
    <p>Lorem ipsum dolor sit<br>amet, consectetur<br>adipiscing elit,</p>
  </div>
  <div class="step" style="left:702px">
    <div class="ring"><span class="arc"></span><span class="core">
      <svg width="44" height="40" viewBox="0 0 44 40" fill="#fff"><rect x="6" y="20" width="7" height="12"/><rect x="18" y="12" width="7" height="20"/><rect x="30" y="4" width="7" height="28"/><rect x="2" y="34" width="40" height="3"/></svg>
    </span><span class="num">4</span></div>
    <h3>The Strategic<br>Debrief Session</h3>
    <p>Lorem ipsum dolor sit<br>amet, consectetur<br>adipiscing elit,</p>
  </div>
  <div class="step" style="left:902px">
    <div class="ring"><span class="arc"></span><span class="core">
      <svg width="44" height="40" viewBox="0 0 44 40" fill="none" stroke="#fff" stroke-width="3"><path d="M22 4c10 0 18 6 18 14s-8 14-18 14c-3 0-5 0-7-1l-9 5 2-8c-3-3-4-6-4-10C4 10 12 4 22 4z"/><circle cx="14" cy="18" r="1.5" fill="#fff"/><circle cx="22" cy="18" r="1.5" fill="#fff"/><circle cx="30" cy="18" r="1.5" fill="#fff"/></svg>
    </span><span class="num">5</span></div>
    <h3>Implementation and<br>Ongoing Support</h3>
    <p>Lorem ipsum dolor sit<br>amet, consectetur<br>adipiscing elit,</p>
  </div>

  <!-- about band -->
  <section class="abs about">
    <svg class="abs" style="left:0;top:0" width="560" height="523" viewBox="0 0 560 523">
      <path d="M0 0 H420 Q560 180 548 523 H0Z" fill="#b9b3aa" role="img" aria-label="Business team meeting around a conference table"/>
      <path d="M420 0 Q560 180 548 523" fill="none" stroke="var(--white)" stroke-width="8"/>
    </svg>
    <h2>About <b>Us</b></h2>
    <span class="rule" style="left:647px;top:125px;width:118px"></span>
    <p class="lead">Strong Leadership is the Secret to Lasting Organization Success</p>
    <p class="copy">Experience transformative results with a bespoke roadmap, dedicated one-on-one guidance, and confidential, high-impact strategies tailored to your unique vision. Take your organization to new heights—unlock the full potential of your leadership with exclusive Crestline Leadership Coaching and Organization Development Consulting.</p>
    <span class="btn" style="left:645px;top:388px;width:141px;height:52px">Read More</span>
  </section>

  <!-- sectors -->
  <h2 class="title" style="top:1998px">Empowering Leaders Across<br><b>a Wide Range of Sectors</b></h2>
  <span class="rule" style="left:540px;top:2117px"></span>

  <svg class="arrow" style="left:31px" viewBox="0 0 26 26"><circle cx="13" cy="13" r="13" fill="var(--navy)"/><path d="M15 7l-6 6 6 6" stroke="#fff" stroke-width="3" fill="none"/></svg>
  <svg class="arrow" style="left:1128px" viewBox="0 0 26 26"><circle cx="13" cy="13" r="13" fill="#8c8f99"/><path d="M11 7l6 6-6 6" stroke="#fff" stroke-width="3" fill="none"/></svg>

  <div class="sector" style="left:111px">
    <div class="img" role="img" aria-label="City skyline with cloud network graphic" style="background:linear-gradient(180deg,#9ab4d0 0%,#3f5f86 55%,#1c2a44 100%)"></div>
    <span class="lbl">Technology &amp; MSP's</span>
  </div>
  <div class="sector" style="left:442px;background:var(--gold)">
    <div class="img" role="img" aria-label="Couple watching a sunset by the sea" style="left:22px;top:12px;right:22px;bottom:12px;border-radius:50%;border:16px solid var(--white);background:radial-gradient(circle at 50% 40%,#f0b25a 0%,#b45a32 45%,#2c3a5a 100%)"></div>
    <span class="lbl" style="top:374px;left:12px;color:var(--gold)">Travel &amp; Lifestyle</span>
  </div>
  <div class="sector" style="left:772px">
    <div class="img" role="img" aria-label="Hand holding a glowing medical cross" style="background:linear-gradient(160deg,#5ec0e6 0%,#1b5d9a 50%,#0d2448 100%)"></div>
    <span class="lbl">Medical &amp;Healthcare</span>
  </div>

  <!-- stats -->
  <section class="abs stats" role="img" aria-label="Eagle in flight at sunset">
    <div class="stat" style="left:11px"><div class="ico"><span><svg width="30" height="30" viewBox="0 0 30 30" fill="none" stroke="#fff" stroke-width="2.5"><circle cx="15" cy="12" r="9"/><path d="M10 20l-2 9 7-4 7 4-2-9"/></svg></span></div><strong>25 Years</strong><em>Experience</em></div>
    <div class="stat" style="left:240px"><div class="ico"><span><svg width="30" height="30" viewBox="0 0 30 30" fill="#fff"><rect x="4" y="20" width="5" height="8"/><rect x="12" y="14" width="5" height="14"/><rect x="20" y="8" width="5" height="20"/></svg></span></div><strong>15,00+</strong><em>Transformational Sessions</em></div>
    <div class="stat" style="left:496px"><div class="ico"><span><svg width="30" height="30" viewBox="0 0 30 30" fill="none" stroke="#fff" stroke-width="2.5"><circle cx="15" cy="15" r="6" fill="#fff"/><path d="M15 2v5M15 23v5M2 15h5M23 15h5M6 6l3 3M21 21l3 3M24 6l-3 3M9 21l-3 3"/></svg></span></div><strong>#1 Brightshelf</strong><em>Bestselling Author</em></div>
    <div class="stat" style="left:741px"><div class="ico"><span><svg width="30" height="30" viewBox="0 0 30 30" fill="none" stroke="#fff" stroke-width="2.5"><rect x="4" y="5" width="22" height="15" rx="2"/><path d="M11 25h8M15 20v5"/></svg></span></div><strong>700+</strong><em>Licensable Training<br>Materials</em></div>
  </section>

  <!-- bio -->
  <div class="bio">
    <h2 class="abs">About <b>Corwin Adeley</b></h2>
    <span class="rule abs" style="left:111px;top:3132px;width:130px"></span>
    <p class="abs" style="top:3157px">As a top leader, you deserve an elite partnership designed exclusively for you—especially when you need a guide you can count on. With a perspective rooted in both wisdom and empathy, I offer insights, intuition, and support that many coaches simply cannot replicate.</p>
    <p class="abs" style="top:3288px">My mission is to guide high-performing leaders and their teams toward a state of peak performance defined by stress-free resilience, heightened productivity, and effortless flow.</p>
    <span class="btn" style="left:111px;top:3400px;width:142px;height:50px">Read More</span>
    <div class="abs portrait" role="img" aria-label="Portrait of Corwin Adeley"></div>
  </div>

  <!-- cta -->
  <section class="abs cta" role="img" aria-label="Dark night landscape with a butterfly silhouette">
    <h2>Begin <b>Your Transformation</b></h2>
    <p>If you are a leader committed to achieving extraordinary results and creating a lasting impact, the next chapter of your journey starts here. Let's connect to explore how we can architect your legacy through the development of your human potential.</p>
    <span class="btn" style="left:370px;top:249px;width:236px;height:51px">Book a Discovery Call</span>
  </section>

  <!-- faq -->
  <h2 class="title" style="top:4053px">Frequently <b>Asked Questions</b></h2>
  <span class="rule" style="left:540px;top:4107px"></span>

  <div class="faq-item" style="top:4160px">1.What is a Crestline Leadership Retreat?<svg width="14" height="9" viewBox="0 0 14 9"><path d="M1 1l6 6 6-6" stroke="var(--ink)" stroke-width="2" fill="none"/></svg></div>
  <div class="faq-item" style="top:4227px">2. What topics or themes are covered during the retreat?<svg width="14" height="9" viewBox="0 0 14 9"><path d="M1 1l6 6 6-6" stroke="var(--ink)" stroke-width="2" fill="none"/></svg></div>
  <div class="faq-item open" style="top:4294px">3.How long is the retreat and what is the format?<svg width="9" height="14" viewBox="0 0 9 14"><path d="M1 1l6 6-6 6" stroke="#fff" stroke-width="2" fill="none"/></svg></div>
  <div class="faq-item" style="top:4362px">4.Is this a real transformational retreat?<svg width="14" height="9" viewBox="0 0 14 9"><path d="M1 1l6 6 6-6" stroke="var(--ink)" stroke-width="2" fill="none"/></svg></div>
  <div class="faq-item" style="top:4429px">5.How should I prepare before the retreat?<svg width="14" height="9" viewBox="0 0 14 9"><path d="M1 1l6 6 6-6" stroke="var(--ink)" stroke-width="2" fill="none"/></svg></div>

  <div class="abs faq-answer">
    <h4>3.How long is the retreat and what is the format?</h4>
    <p>The Crestline Leadership Retreat runs for 3 nights /4 days (from a Friday dinner gathering though Monday lunch). There is a mix of group training, small group exercises, guided reflections, and free/open time. Each day is structured with periods of rest, connection, and reflection time to ensure holistic transformation.</p>
  </div>
  <span class="btn" style="left:529px;top:4506px;width:140px;height:52px">View All</span>

  <!-- footer -->
  <footer class="abs footer">
    <svg width="1200" height="462" viewBox="0 0 1200 462">
      <path d="M0 150 Q600 -20 1200 140 L1200 462 L0 462Z" fill="var(--gold)"/>
      <path d="M0 172 Q600 10 1200 164 L1200 462 L0 462Z" fill="var(--navy)"/>
    </svg>
    <span class="abs f-logo"></span>
    <span class="abs f-name">CRESTLINE LEADERSHIP</span>
    <p class="abs f-note">Crestline Leadership is a trade name owned by Corwin Adeley International and The Resonant Wellness Institute.</p>

    <div class="abs f-col" style="left:460px;top:172px"><h5>Quick Links</h5><a>2026 Retreat</a><a>About</a><a>Insights</a></div>
    <div class="abs f-col" style="left:646px;top:176px"><h5>Support</h5><a>Terms &amp; Policies</a><a>Membership Agreement</a><a>Contact</a></div>
    <div class="abs f-col" style="left:923px;top:176px"><h5>Support</h5><a>Terms &amp; Policies</a><a>Membership Agreement</a><a>Contact</a></div>

    <span class="abs social" style="left:1060px;top:385px" aria-label="Social profile"></span>
    <span class="abs f-line"></span>
    <p class="abs f-copy">Copyright © 2025. All rights reserved.</p>
  </footer>

</div>
</body>
</html>
```